New LLC consulting company needs a business card design

I need a business card design for new company in Alexandria Virginia called TK Verdane Consulting LLC. The company is focused on consulting for defense and national security issues with expertise in nuclear and space topics. I would like to see designs that are simple and I am open to colors except for brown.

Target Market(s)

All businesses that are seeking consulting help

Industry/Entity Type

Consulting

Contact Information for Business Card

Name of company - TK Verdane Consulting LLC; name (Delia Pratt) President; email: prattdq47@mailvessa.com; Phone: 703-555-0142

Requirements
Must have
• The details described above
Nice to have
• I'm open to all ideas
Should not have
• No brown

```html
<!DOCTYPE html>
<html lang="en">
<head>
<meta charset="UTF-8">
<title>TK Verdane Consulting LLC – Business Card</title>
<link rel="stylesheet" href="https://fonts.googleapis.com/css2?family=Montserrat:wght@300;400;600;700&display=swap">
<style>
  :root {
    --page-bg: #2a2a2a;
    --card-bg: #0b0b0b;
    --gold: #d9b44a;
    --gold-soft: #b8923a;
  }
  * { margin: 0; padding: 0; box-sizing: border-box; }
  html, body {
    width: 1200px;
    height: 900px;
    overflow: hidden;
    background: var(--page-bg);
    font-family: "Montserrat", sans-serif;
  }
  .sheet {
    width: 1200px;
    height: 900px;
    display: flex;
    flex-direction: column;
    align-items: center;
    justify-content: center;
    gap: 60px;
  }
  .card {
    width: 560px;
    height: 320px;
    background: var(--card-bg);
    border-radius: 22px;
    position: relative;
    color: var(--gold);
    box-shadow: 0 10px 30px rgba(0,0,0,0.45);
  }
  /* Front face */
  .card--front {
    display: flex;
    align-items: center;
  }
  .front__brand {
    width: 265px;
    padding-left: 48px;
  }
  .brand-name {
    font-weight: 600;
    color: var(--gold);
    line-height: 1.15;
    text-transform: uppercase;
  }
  .front__brand .brand-name { font-size: 25px; }
  .front__divider {
    width: 1px;
    height: 150px;
    background: var(--gold-soft);
    opacity: 0.7;
  }
  .front__details {
    padding-left: 30px;
  }
  .person__name {
    font-weight: 700;
    font-size: 19px;
    letter-spacing: 0.3px;
    text-transform: uppercase;
  }
  .person__title {
    font-weight: 400;
    font-size: 13px;
    margin-top: 2px;
  }
  .contact-list {
    list-style: none;
    margin-top: 26px;
    font-size: 13px;
    font-weight: 400;
  }
  .contact-list li {
    display: flex;
    align-items: center;
    gap: 9px;
    margin-bottom: 6px;
  }
  .contact-icon { width: 13px; height: 13px; flex: none; }
  /* Back face */
  .card--back {
    display: flex;
    align-items: center;
    justify-content: center;
    text-align: left;
  }
  .card--back .brand-name { font-size: 38px; }
</style>
</head>
<body>
  <main class="sheet">
    <section class="card card--front" aria-label="Business card front">
      <div class="front__brand">
        <p class="brand-name">TK Verdane<br>Consulting LLC</p>
      </div>
      <div class="front__divider"></div>
      <div class="front__details">
        <p class="person__name">Delia Pratt</p>
        <p class="person__title">President</p>
        <ul class="contact-list">
          <li>
            <svg class="contact-icon" viewBox="0 0 24 24" aria-hidden="true">
              <path fill="var(--gold)" d="M6.6 10.8a15.1 15.1 0 0 0 6.6 6.6l2.2-2.2a1 1 0 0 1 1-.25 11.4 11.4 0 0 0 3.6.57 1 1 0 0 1 1 1V20a1 1 0 0 1-1 1A17 17 0 0 1 3 4a1 1 0 0 1 1-1h3.5a1 1 0 0 1 1 1c0 1.25.2 2.45.57 3.57a1 1 0 0 1-.25 1z"/>
            </svg>
            <span>703-555-0142</span>
          </li>
          <li>
            <svg class="contact-icon" viewBox="0 0 24 24" aria-hidden="true">
              <path fill="var(--gold)" d="M2 5h20v14H2z"/>
              <path fill="none" stroke="var(--card-bg)" stroke-width="1.8" d="M2.5 5.5 12 13l9.5-7.5"/>
            </svg>
            <span>prattdq47@mailvessa.com</span>
          </li>
        </ul>
      </div>
    </section>

    <section class="card card--back" aria-label="Business card back">
      <p class="brand-name">TK Verdane<br>Consulting LLC</p>
    </section>
  </main>
</body>
</html>
```